Federal IT Consulting Company - Brisolux Consulting Group

We're seeking a skilled web designer to create a modern, bold, and engaging WordPress website for Brisolux Consulting Group, LLC. Our company specializes in federal IT consulting, and our name is a play on "Brightening Solutions." The website should reflect our expertise in the federal technology marketplace and position us as a trusted partner for clients navigating their IT journey.

contact: info@brisoluxgrp-example.com

Current Status

WordPress is already installed on our hosting account
We have an existing logo (may need modernization)

Design Requirements

Style:

Modern and visually striking design
Bold elements to convey confidence and expertise
Incorporate the concept of "brightening solutions" into the design

Features:

Modern UX sliders for dynamic content presentation
Eye-catching, high-quality images (stock photos to be sourced by the designer)
Responsive design for all devices

Color Scheme:

To be proposed by the designer, should align with our brand and convey trust and technological expertise

Logo:

Evaluate our current logo
Create a transparent background version if needed
Propose modernization if deemed necessary

Accessibility:

Ensure design elements are accessible to users with disabilities
Use high contrast ratios for text and background colors
Provide text alternatives for non-text content

Website Structure
Create the following pages, with the possibility of subpages:

Home
Services
About
Contact

Specific Page Requirements
Home Page

Striking hero section with a clear value proposition
Overview of our services
Client testimonials or trust indicators

Services Page

Detailed list of our IT consulting services
Clear explanation of how we help navigate the federal IT landscape

About Page

Company history and mission
Team highlights (if applicable)
Our approach to federal IT consulting

Contact Page

Contact form
Other contact methods (phone, email)

Technical Requirements

Fully responsive design
SEO best practices implemented
Fast loading times
Integration with necessary plugins (to be discussed)
Training on how to update and maintain the site
Full compliance with Web Content Accessibility Guidelines (WCAG) 2.1 Level AA
Adherence to Section 508 standards for federal website accessibility
Implementation of necessary features for ADA compliance
Updates

Designs look the same

Target Market(s)

US Federal Govt customers looking for IT support.

Industry/Entity Type

IT Consulting

Coding

Coded - Design and coding required

Colors
0054AA
0677BA
7BADD7
CADEEF
E8F1F8
0094D4
00A9DD
6FCCEA
C7EBF8
E9F6FB
00AB8E
00BBA5
67D7C9
C6EFE9
E9F9F6

```html
<!DOCTYPE html>
<html lang="en">
<head>
<meta charset="utf-8">
<title>Brisolux Federal Services</title>
<link rel="stylesheet" href="https://fonts.googleapis.com/css2?family=Michroma&family=Roboto:ital,wght@0,400;0,500;0,700;1,400;1,500&display=swap">
<style>
:root{
  --blue:#0094D4;
  --blue-bright:#00A9DD;
  --blue-deep:#0677BA;
  --sky:#C7EBF8;
  --sky-soft:#E9F6FB;
  --ink:#111418;
  --text:#555b62;
  --white:#ffffff;
  --black:#000000;
  --star:#E0B21A;
}
*{margin:0;padding:0;box-sizing:border-box}
html,body{width:1200px;height:3283px;overflow:hidden;background:var(--white)}
body{font-family:"Roboto",Arial,sans-serif;color:var(--ink)}
.page{position:relative;width:1200px;height:3283px;overflow:hidden;background:var(--white)}
.abs{position:absolute}
.display{font-family:"Michroma","Arial Black",sans-serif;font-weight:400;letter-spacing:1px}
.btn{position:absolute;display:flex;align-items:center;justify-content:center;background:var(--blue);color:var(--white);font-weight:700;font-size:15px;border-radius:24px;text-transform:uppercase}

/* header */
.site-header{position:absolute;left:0;top:0;width:1200px;height:82px;background:var(--white);border-top:3px solid var(--blue);z-index:5}
.brand{position:absolute;left:146px;top:20px;display:flex;align-items:center;gap:10px;font-family:"Michroma",sans-serif;font-size:30px;color:var(--ink)}
.brand .dot{width:34px;height:34px;border-radius:50%;border:5px solid var(--blue)}
.main-nav{position:absolute;left:600px;top:34px;display:flex;gap:36px;font-size:14px;font-weight:500;text-transform:uppercase}
.main-nav .active{color:var(--ink)}
.login{left:956px;top:20px;width:100px;height:42px;font-size:14px;gap:8px}

/* hero */
.hero-photo{position:absolute;left:0;top:82px;width:1200px;height:670px;background:radial-gradient(ellipse at 30% 40%,#56677a 0%,#2b3746 45%,#161d27 100%)}
.hero-badge{position:absolute;left:614px;top:148px;width:438px;height:438px;border-radius:50%;background:var(--blue);display:flex;align-items:center;justify-content:center}
.hero-badge .inner{width:370px;height:370px;border-radius:50%;background:var(--white);border:5px solid var(--blue);outline:10px solid var(--white);display:flex;flex-direction:column;align-items:center;justify-content:center;text-align:center}
.hero-badge .t{font-family:"Michroma",sans-serif;font-size:37px;line-height:44px;color:var(--ink)}
.hero-badge .t.b{color:var(--blue)}
.hero-badge .btn{position:static;width:158px;height:52px;font-size:18px;font-weight:500;border-radius:14px;margin-top:22px}
.dots{position:absolute;left:568px;top:667px;display:flex;gap:14px}
.dots i{width:11px;height:11px;border-radius:3px;background:var(--white)}
.dots i.on{background:var(--blue)}

/* welcome */
.section-title{position:absolute;left:0;width:1200px;text-align:center;font-family:"Michroma",sans-serif}
.rule{position:absolute;left:581px;width:38px;height:3px;background:var(--blue)}
.welcome-copy{position:absolute;top:946px;width:414px;font-size:14.5px;line-height:26.4px;color:var(--text);text-align:justify}

/* services */
.svc{position:absolute;width:230px;text-align:center}
.svc svg{display:block;margin:0 auto 14px}
.svc h3{font-size:15.5px;font-weight:500;margin-bottom:10px;color:var(--ink)}
.svc p{font-size:12px;line-height:18px;color:var(--text)}
.svc a{display:inline-block;margin-top:12px;font-size:12px;font-weight:500;color:var(--blue);text-decoration:underline}
.svc-hub{position:absolute;left:484px;top:1602px;width:250px;height:250px;border-radius:50%;border:10px solid var(--blue);background:var(--white);display:flex;align-items:center;justify-content:center;font-family:"Michroma",sans-serif;font-size:24px;color:var(--ink);outline:6px solid var(--white);outline-offset:-22px}

/* testimonials */
.avatar{position:absolute;border-radius:50%}
.quote-mark{position:absolute;left:516px;top:2305px;font-family:Georgia,serif;font-size:96px;line-height:1;color:var(--blue);font-weight:700}
.quote{position:absolute;left:519px;top:2363px;width:520px;font-style:italic;font-size:15px;line-height:27px;color:var(--text);text-align:justify}
.author{position:absolute;left:519px;top:2515px;font-size:19px;font-style:italic;color:var(--text)}
.author b{font-style:normal;color:var(--blue);font-weight:700}
.stars{position:absolute;left:519px;top:2553px;display:flex;gap:7px}
.arrow-btn{position:absolute;left:1094px;width:44px;height:44px;border-radius:50%;border:1.5px solid #777;display:flex;align-items:center;justify-content:center}

/* footer */
.footer-brand{position:absolute;left:0;top:2905px;width:1200px;display:flex;justify-content:center;align-items:center;gap:14px;font-family:"Michroma",sans-serif;font-size:52px;color:var(--white)}
.footer-brand .dot{width:52px;height:52px;border-radius:50%;border:7px solid var(--blue)}
.footer-rule{position:absolute;left:144px;top:3026px;width:912px;height:1px;background:#3a3a3a}
.contact-item{position:absolute;top:3045px;display:flex;align-items:center;gap:14px;color:var(--white);font-size:13.5px;line-height:22px}
.contact-item .ic{width:40px;height:40px;border-radius:50%;border:1.5px solid var(--white);display:flex;align-items:center;justify-content:center;flex:none}
.footer-nav{position:absolute;left:143px;top:3150px;display:flex;gap:38px;color:var(--white);font-weight:700;font-size:15px}
.copyright{position:absolute;right:144px;top:3152px;color:var(--white);font-size:13px}
.social{position:absolute;left:503px;top:3208px;display:flex;gap:10px}
.social span{width:30px;height:30px;border-radius:50%;border:1.5px solid var(--white)}
.sr{position:absolute;width:1px;height:1px;overflow:hidden;clip:rect(0 0 0 0)}
</style>
</head>
<body>
<div class="page">

  <header class="site-header">
    <div class="brand"><span class="dot"></span>BRISOLUX</div>
    <nav class="main-nav"><span class="active">Home</span><span>Services</span><span>About</span><span>Contact</span></nav>
    <div class="btn login">
      <svg width="14" height="14" viewBox="0 0 14 14" aria-hidden="true"><circle cx="7" cy="4" r="3.2" fill="#fff"/><path d="M1 14c0-4 3-6 6-6s6 2 6 6z" fill="#fff"/></svg>Login
    </div>
  </header>

  <!-- hero -->
  <div class="hero-photo" role="img" aria-label="Hand working on a laptop showing financial charts"></div>
  <svg class="abs" style="left:0;top:0" width="1200" height="780" aria-hidden="true">
    <path d="M0,484 Q600,986 1200,484 L1200,780 L0,780 Z" fill="#fff"/>
    <path d="M230,640 Q600,880 970,640" fill="none" stroke="var(--blue)" stroke-width="0"/>
    <path d="M0,484 Q600,986 1200,484" fill="none" stroke="var(--blue)" stroke-width="14" stroke-dasharray="0 330 540 2000"/>
    <path d="M590,732 L600,742 L610,732 Z" fill="var(--blue)"/>
  </svg>
  <div class="hero-badge">
    <div class="inner">
      <div class="t">BRISOLUX</div>
      <div class="t b">FEDERAL</div>
      <div class="t">SERVICES</div>
      <div class="btn">Get Started</div>
    </div>
  </div>
  <div class="dots"><i></i><i class="on"></i><i></i></div>

  <!-- welcome -->
  <h1 class="section-title" style="top:816px;font-size:34px">WELCOME TO</h1>
  <h2 class="section-title" style="top:864px;font-size:22px;color:var(--blue)">BRISOLUX FEDERAL SERVICES</h2>
  <div class="rule" style="top:904px"></div>
  <p class="welcome-copy" style="left:156px">Sed ut perspiciatis unde omnis iste natus error sit voluptatem accusantium doloremque laudantium, totam rem aperiam, eaque ipsa quae ab illo inventore veritatis et quasi architecto beatae vitae dicta sunt explicabo. Nemo enim ipsam voluptatem quia voluptas sit aspernatur aut odit aut fugit, sed quia consequuntur magni dolores eos qui ratione voluptatem sequi nesciunt. Neque porro quisquam est, qui dolorem ipsum quia dolor sit amet, consectetur, adipisci velit, sed quia non numquam eius modi tempora incidunt ut labore et dolore magnam</p>
  <p class="welcome-copy" style="left:631px">Sed ut perspiciatis unde omnis iste natus error sit voluptatem accusantium doloremque laudantium, totam rem aperiam, eaque ipsa quae ab illo inventore veritatis et quasi architecto beatae vitae dicta sunt explicabo. Nemo enim ipsam voluptatem quia voluptas sit aspernatur aut odit aut fugit, sed quia consequuntur magni dolores eos qui ratione voluptatem sequi nesciunt. Neque porro quisquam est, qui dolorem ipsum quia dolor sit amet, consectetur, adipisci velit, sed quia non numquam eius modi tempora incidunt ut labore et dolore magnam</p>
  <div class="btn" style="left:534px;top:1209px;width:132px;height:44px;font-size:14px">Read More</div>

  <!-- services -->
  <svg class="abs" style="left:0;top:1320px" width="1200" height="820" role="img" aria-label="Team of colleagues collaborating in a bright office">
    <defs>
      <linearGradient id="svcBg" x1="0" y1="0" x2="0" y2="1">
        <stop offset="0" stop-color="#dff1f9"/><stop offset="1" stop-color="#c7e6f4"/>
      </linearGradient>
    </defs>
    <path d="M0,260 Q600,-238 1200,260 L1200,560 Q600,1056 0,560 Z" fill="url(#svcBg)"/>
    <path d="M0,260 Q600,-238 1200,260" fill="none" stroke="var(--blue)" stroke-width="12" stroke-dasharray="0 300 700 2000"/>
    <path d="M0,560 Q600,1056 1200,560" fill="none" stroke="var(--blue)" stroke-width="12" stroke-dasharray="0 300 700 2000"/>
    <path d="M0,260 Q600,-238 1200,260" fill="none" stroke="var(--blue)" stroke-width="2"/>
    <path d="M0,560 Q600,1056 1200,560" fill="none" stroke="var(--blue)" stroke-width="2"/>
  </svg>
  <h2 class="section-title" style="top:1468px;font-size:34px">OUR SERVICES</h2>
  <div class="rule" style="top:1516px"></div>

  <div class="svc" style="left:243px;top:1540px">
    <svg width="44" height="42" viewBox="0 0 44 42" fill="none" stroke="var(--blue)" stroke-width="2"><rect x="2" y="6" width="40" height="26" rx="2"/><path d="M16 40h12M22 32v8"/><circle cx="30" cy="10" r="6"/></svg>
    <h3>IT CONSULTING</h3>
    <p>Sed ut perspiciatis unde omnis iste natus error sit voluptatem accusantium doloremque laudatam rem</p>
    <a>READ MORE</a>
  </div>
  <div class="svc" style="left:727px;top:1540px">
    <svg width="44" height="42" viewBox="0 0 44 42" fill="none" stroke="#222" stroke-width="2"><path d="M22 2l16 6v12c0 10-8 18-16 20C14 38 6 30 6 20V8z"/><circle cx="26" cy="20" r="6"/></svg>
    <h3>MVOLUPTATE</h3>
    <p>Sed ut perspiciatis unde omnis iste natus error sit voluptatem accusantium doloremque laudatam rem</p>
    <a>READ MORE</a>
  </div>
  <div class="svc" style="left:243px;top:1762px">
    <svg width="50" height="46" viewBox="0 0 50 46" fill="none" stroke="#222" stroke-width="2"><circle cx="25" cy="23" r="16"/><rect x="15" y="14" width="20" height="5"/><rect x="15" y="21" width="20" height="5"/><rect x="15" y="28" width="20" height="5"/></svg>
    <h3>ARCHITECTO BEATAE</h3>
    <p>Sed ut perspiciatis unde omnis iste natus error sit voluptatem accusantium doloremque laudatam rem</p>
    <a>READ MORE</a>
  </div>
  <div class="svc" style="left:727px;top:1762px">
    <svg width="50" height="46" viewBox="0 0 50 46" fill="none" stroke="#222" stroke-width="2"><circle cx="28" cy="14" r="10"/><path d="M4 36h10l10 4 20-8M4 30h14l8 2"/></svg>
    <h3>NEQUE PORRO</h3>
    <p>Sed ut perspiciatis unde omnis iste natus error sit voluptatem accusantium doloremque laudatam rem</p>
    <a>READ MORE</a>
  </div>

  <div class="svc-hub">BRISOLUX</div>
  <div class="btn" style="left:482px;top:1954px;width:236px;height:44px;font-size:14px">View More Services</div>

  <!-- testimonials -->
  <h2 class="section-title" style="top:2196px;font-size:34px">CUSTOMER TESTIMONIALS</h2>
  <div class="rule" style="top:2251px"></div>

  <div class="avatar" style="left:173px;top:2299px;width:80px;height:80px;background:linear-gradient(#d7b46a,#b48a2e)" role="img" aria-label="Portrait of a smiling customer"></div>
  <div class="avatar" style="left:164px;top:2429px;width:80px;height:80px;background:linear-gradient(#9fb3c6,#4e6277)" role="img" aria-label="Portrait of an older customer"></div>
  <div class="avatar" style="left:221px;top:2533px;width:80px;height:80px;background:linear-gradient(#7a8b7a,#2f5146)" role="img" aria-label="Portrait of a customer"></div>
  <div class="avatar" style="left:340px;top:2565px;width:80px;height:80px;background:linear-gradient(#b9a48e,#8a1f2a)" role="img" aria-label="Portrait of a customer"></div>
  <div class="avatar" style="left:256px;top:2320px;width:220px;height:220px;border:9px solid var(--blue);background:var(--white);padding:10px">
    <div style="width:100%;height:100%;border-radius:50%;background:linear-gradient(#dfe2e5,#a99a80)" role="img" aria-label="Portrait of the featured customer"></div>
  </div>

  <div class="quote-mark">&ldquo;</div>
  <p class="quote">Sed ut perspiciatis unde omnis iste natus error sit voluptatem accusantium doloremque laudatam remaperiam, eaque ipsa quaeSed ut perspiciatis unde omnis iste natus error sit voluptatem accusantium doloremque laudatam rem aperiam, eaque ipsa quaeSed ut perspiciatis unde omnis iste natus error sit voluptatem accusantium datam remaperiam, eaque ipsa quae</p>
  <div class="author"><b>- JORDAN REYES</b>,Customer</div>
  <div class="stars">
    <svg width="150" height="24" viewBox="0 0 150 24" fill="var(--star)" aria-label="5 stars" role="img">
      <g id="st"><path d="M12 1l3.4 7 7.6 1-5.5 5.3 1.3 7.6L12 18.3 5.2 21.9l1.3-7.6L1 9l7.6-1z"/></g>
      <use href="#st" x="30"/><use href="#st" x="60"/><use href="#st" x="90"/><use href="#st" x="120"/>
    </svg>
  </div>
  <div class="arrow-btn" style="top:2373px"><svg width="18" height="10" viewBox="0 0 18 10" fill="none" stroke="#444" stroke-width="2"><path d="M1 9l8-8 8 8"/></svg></div>
  <div class="arrow-btn" style="top:2429px"><svg width="18" height="10" viewBox="0 0 18 10" fill="none" stroke="#444" stroke-width="2"><path d="M1 1l8 8 8-8"/></svg></div>
  <div class="btn" style="left:482px;top:2634px;width:236px;height:44px;font-size:14px">View More Testimonials</div>

  <!-- footer -->
  <svg class="abs" style="left:0;top:2760px" width="1200" height="523" aria-hidden="true">
    <path d="M0,260 Q600,-236 1200,260 L1200,523 L0,523 Z" fill="var(--black)"/>
    <path d="M0,260 Q600,-236 1200,260" fill="none" stroke="var(--blue)" stroke-width="14"/>
    <path d="M590,16 L600,6 L610,16 Z" fill="var(--blue)"/>
  </svg>
  <div class="footer-brand"><span class="dot"></span>BRISOLUX</div>
  <div class="footer-rule"></div>

  <div class="contact-item" style="left:196px">
    <span class="ic"><svg width="14" height="18" viewBox="0 0 14 18" fill="#fff"><path d="M7 0a7 7 0 0 0-7 7c0 5 7 11 7 11s7-6 7-11a7 7 0 0 0-7-7zm0 10a3 3 0 1 1 0-6 3 3 0 0 1 0 6z"/></svg></span>
    <span>314,At vero eos et accu<br>samus et iusto odio dimos ducimu</span>
  </div>
  <div class="contact-item" style="left:518px;font-weight:700;font-size:15px">
    <span class="ic" style="border-color:var(--blue)"><svg width="18" height="18" viewBox="0 0 18 18" fill="#fff"><path d="M4 1l3 4-2 2c1 2 3 4 5 5l2-2 4 3-2 3C8 16 2 10 1 3z"/></svg></span>
    <span>+1 555 010 0199</span>
  </div>
  <div class="contact-item" style="left:742px">
    <span class="ic"><svg width="18" height="14" viewBox="0 0 18 14" fill="#fff"><path d="M0 0h18v2L9 8 0 2zM0 4l9 6 9-6v10H0z"/></svg></span>
    <span>info@brisoluxfederal-example.com</span>
  </div>

  <nav class="footer-nav"><span>HOME</span><span>SERVICES</span><span>ABOUT</span><span>CONTACT</span></nav>
  <div class="copyright">&copy; 2024 Brisolux Federal Services, LLC. All rights reserved.Privacy &nbsp;|&nbsp; Terms of Use</div>
  <div class="social" aria-label="Social media links">
    <span><i class="sr">Social link</i></span><span><i class="sr">Social link</i></span><span><i class="sr">Social link</i></span><span><i class="sr">Social link</i></span><span><i class="sr">Social link</i></span>
  </div>

</div>
</body>
</html>
```